New Business Card for Web Design/Internet Marketing Company

Looking for a great looking new business card. We are a 10 year old web design, internet marketing and website management company that works mostly with small businesses.

Our new card needs to better match the colors and style of our website, be bold, extremely usable and slightly edgy.

Target Market(s)

Small/Medium businesses that have websites

Industry/Entity Type

Internet

Requirements
Must have
• Front and back design, full color, rounded corners please

Must use the colors/style of our website (JPG provided)

INFO FOR CARDS (as readable as possible please)
Mark Lenner
President/CEO
mark@trelvanmedia.example
Phone: 520-381-7459
Toll Free: 866-381-7459
Address: 4315 W. Calloway Ave. Ste. 140, Tucson, AZ 85792

THINGS I WANT TO PROMOTE (if there is room):
1. Our Website - www.trelvanmedia.example

2. Social Media
Twitter: @trelvanmedia
Facebook: www.facebook.com/trelvanmedia

3. Our Services
Web Design
Internet Marketing
Website Management

```html
<!DOCTYPE html>
<html lang="en">
<head>
<meta charset="utf-8">
<title>Trelvan Media – Business Card</title>
<link rel="stylesheet" href="https://fonts.googleapis.com/css2?family=Open+Sans:wght@400;600;700&display=swap">
<style>
  :root {
    --bg: #e6e3df;
    --card: #ffffff;
    --blue: #1b8fca;
    --orange: #f5883a;
    --ink: #4a4a4a;
    --ink-soft: #5c5c5c;
  }
  * { box-sizing: border-box; margin: 0; padding: 0; }
  html, body { width: 1200px; height: 402px; overflow: hidden; }
  body {
    background: var(--bg);
    font-family: "Open Sans", Arial, sans-serif;
    color: var(--ink);
    position: relative;
  }
  .card {
    position: absolute;
    top: 56px;
    width: 512px;
    height: 293px;
    background: var(--card);
    border-radius: 10px;
    box-shadow: 0 2px 6px rgba(0,0,0,.18);
    overflow: hidden;
  }
  .card--front { left: 68px; }
  .card--back { left: 620px; }

  .brand {
    position: absolute;
    display: flex;
    align-items: center;
    gap: 10px;
    color: var(--orange);
    font-weight: 700;
    white-space: nowrap;
  }
  .brand__dot { border-radius: 50%; background: var(--orange); flex: none; }
  .card--front .brand { left: 28px; top: 80px; font-size: 32px; }
  .card--front .brand__dot { width: 16px; height: 16px; }
  .card--back .brand { left: 34px; top: 58px; font-size: 44px; }
  .card--back .brand__dot { width: 22px; height: 22px; }

  .rule { position: absolute; height: 1.5px; background: var(--blue); }

  .address {
    position: absolute;
    right: 36px;
    top: 104px;
    text-align: right;
    font-size: 12.5px;
    line-height: 17px;
    color: var(--ink);
  }
  .person { position: absolute; right: 36px; top: 167px; text-align: right; }
  .person__name { color: var(--blue); font-weight: 600; font-size: 17px; line-height: 22px; }
  .person__title { font-size: 12.5px; line-height: 16px; }

  .contacts {
    position: absolute;
    right: 36px;
    top: 210px;
    list-style: none;
    font-size: 12.5px;
    line-height: 18.3px;
  }
  .contacts li, .social li { display: flex; justify-content: flex-end; align-items: center; gap: 5px; }
  .icon { width: 10px; height: 10px; flex: none; }

  .social {
    position: absolute;
    right: 36px;
    top: 120px;
    list-style: none;
    font-size: 12.5px;
    line-height: 17.5px;
  }
  .social__mark { width: 12px; height: 12px; border-radius: 2px; background: var(--blue); flex: none; }

  .services-title {
    position: absolute;
    right: 36px;
    top: 180px;
    color: var(--blue);
    font-weight: 600;
    font-size: 20px;
    line-height: 26px;
  }
  .services {
    position: absolute;
    right: 38px;
    top: 213px;
    list-style: none;
    text-align: right;
    font-size: 16.5px;
    line-height: 22.5px;
    color: var(--ink-soft);
  }
</style>
</head>
<body>

<section class="card card--front" aria-label="Card front">
  <div class="brand"><span class="brand__dot"></span>Trelvan Media</div>

  <address class="address">
    4315 W. Calloway Ave.<br>
    Ste. 140<br>
    Tucson, AZ 85792
  </address>

  <div class="rule" style="left:0; width:384px; top:178px;"></div>
  <div class="rule" style="left:492px; width:20px; top:178px;"></div>

  <div class="person">
    <div class="person__name">Mark Lenner</div>
    <div class="person__title">President/CEO</div>
  </div>

  <ul class="contacts">
    <li>520-381-7459
      <svg class="icon" viewBox="0 0 10 10" aria-hidden="true"><circle cx="5" cy="5" r="5" fill="var(--blue)"/><path d="M3 2.6l1 1-.6.8a4 4 0 0 0 2.2 2.2l.8-.6 1 1-.8.9A5 5 0 0 1 2.1 3.4z" fill="#fff"/></svg>
    </li>
    <li>866-381-7459
      <svg class="icon" viewBox="0 0 10 10" aria-hidden="true"><circle cx="5" cy="5" r="5" fill="var(--blue)"/><path d="M3 2.6l1 1-.6.8a4 4 0 0 0 2.2 2.2l.8-.6 1 1-.8.9A5 5 0 0 1 2.1 3.4z" fill="#fff"/></svg>
    </li>
    <li>mark@trelvanmedia.example
      <svg class="icon" viewBox="0 0 10 10" aria-hidden="true"><rect x="0.5" y="2" width="9" height="6.5" rx="0.8" fill="var(--blue)"/><path d="M1 2.6l4 3 4-3" stroke="#fff" stroke-width="0.8" fill="none"/></svg>
    </li>
    <li>www.trelvanmedia.example
      <svg class="icon" viewBox="0 0 10 10" aria-hidden="true"><circle cx="5" cy="5" r="4.4" fill="none" stroke="var(--blue)" stroke-width="1.1"/><ellipse cx="5" cy="5" rx="1.9" ry="4.4" fill="none" stroke="var(--blue)" stroke-width="0.9"/><path d="M0.6 5h8.8" stroke="var(--blue)" stroke-width="0.9"/></svg>
    </li>
  </ul>
</section>

<section class="card card--back" aria-label="Card back">
  <div class="brand"><span class="brand__dot"></span>Trelvan Media</div>

  <ul class="social">
    <li><span class="social__mark"></span>@trelvanmedia</li>
    <li><span class="social__mark"></span>trelvanmedia</li>
  </ul>

  <div class="rule" style="left:0; width:332px; top:193px;"></div>
  <div class="rule" style="left:490px; width:22px; top:193px;"></div>
  <h2 class="services-title">Our Services</h2>

  <ul class="services">
    <li>Web Design</li>
    <li>Internet Marketing</li>
    <li>Website Management</li>
  </ul>
</section>

</body>
</html>
```